Dynamic Business Card for Sports Supplements Company

Hi! I'm looking for an awesome business card to match my existing sports supplement company. I have uploaded my current company logo and screenshot of the front page of my website.

I would like to have something dynamic and interesting and utilize the colors in the website - the reds and purples

The business card should be double sided and focus on a unique eye-catching design on the back and include all the relevant company info.

Most importantly, it should say somewhere: "Sign up on our website for a coupon code."

Target Market(s)

Mostly for women gym goers but it shouldn't be too feminine. It should be in keeping with the website design. It should flow and clearly be connected to it

Industry/Entity Type

Business

Contact Information for Business Card

Lorraine K. Vestal
CEO
LVestal@Quorvanexco.com
www.quorvanexco.com
555.417.3820
P.O. Box 47315
Larkmoor, Vermont 00000

Sign up on our website for a coupon code

Font styles to use
Serif
Sans Serif
Other font styles liked:
• Novecento font family and "Quorvanex" is in AR Destine font

Requirements
Must have
• One side should be a bold Quorvanex logo design. Even just the symbol itself may be o.k. (see attached file)

```html
<!DOCTYPE html>
<html lang="en">
<head>
<meta charset="utf-8">
<title>Quorvanex Business Card</title>
<link href="https://fonts.googleapis.com/css2?family=Saira:wght@400;500;700&family=Lato:wght@400;700&display=swap" rel="stylesheet">
<style>
  :root {
    --backdrop: #c8c8c8;
    --card-light: #ffffff;
    --card-dark: #1c1c1c;
    --card-dark-edge: #111111;
    --ink: #1a1a1a;
    --ink-soft: #2b2b2b;
    --accent: #e3161c;
    --rule: #ec8a8d;
    --light-text: #ffffff;
  }
  * { margin: 0; padding: 0; box-sizing: border-box; }
  html, body { width: 1200px; height: 900px; overflow: hidden; }
  body { background: var(--backdrop); position: relative; font-family: "Lato", sans-serif; }

  .card {
    position: absolute;
    top: 271px;
    width: 457px;
    height: 281px;
    border-radius: 14px;
    box-shadow: 3px 4px 6px rgba(0,0,0,0.35);
  }
  .card--front { left: 137px; background: var(--card-light); }
  .card--back {
    left: 627px;
    background: radial-gradient(ellipse at 50% 40%, #2a2a2a 0%, var(--card-dark) 55%, var(--card-dark-edge) 100%);
  }

  .wordmark {
    position: absolute;
    font-family: "Saira", sans-serif;
    font-weight: 700;
    letter-spacing: 0.5px;
    line-height: 1;
    display: flex;
    align-items: center;
    gap: 8px;
    white-space: nowrap;
  }
  .wordmark__square { background: var(--accent); flex: none; }
  .tagline {
    position: absolute;
    font-family: "Saira", sans-serif;
    font-weight: 500;
    line-height: 1;
    white-space: nowrap;
  }

  /* Front */
  .card--front .wordmark { left: 27px; top: 74px; font-size: 27px; color: var(--ink); }
  .card--front .wordmark__square { width: 14px; height: 14px; }
  .card--front .tagline { left: 27px; top: 100px; font-size: 8px; letter-spacing: 1.7px; color: var(--ink); }

  .holder-name {
    position: absolute; left: 27px; top: 148px;
    font-family: "Saira", sans-serif; font-weight: 500;
    font-size: 18px; letter-spacing: 1.6px; color: var(--accent);
    text-transform: uppercase; line-height: 1; white-space: nowrap;
  }
  .holder-role {
    position: absolute; left: 27px; top: 170px;
    font-family: "Saira", sans-serif; font-weight: 400;
    font-size: 13px; color: var(--ink); line-height: 1;
  }
  .holder-rule {
    position: absolute; left: 63px; top: 176px; width: 365px; height: 1px;
    background: var(--rule);
  }

  .contact-list { position: absolute; left: 27px; top: 197px; list-style: none; }
  .contact-list li {
    display: flex; align-items: center; gap: 8px;
    font-size: 13px; color: var(--ink-soft); height: 21px; white-space: nowrap;
  }
  .contact-list svg { width: 11px; height: 11px; fill: var(--accent); flex: none; }

  .postal {
    position: absolute; right: 27px; top: 223px; text-align: right;
    font-size: 13px; color: var(--ink-soft); line-height: 17px; font-style: normal;
    white-space: nowrap;
  }

  /* Back */
  .card--back .wordmark {
    left: 0; right: 0; top: 165px; justify-content: center;
    font-size: 30px; color: var(--light-text);
  }
  .card--back .wordmark__square { width: 16px; height: 16px; }
  .card--back .tagline {
    left: 0; right: 0; top: 193px; text-align: center;
    font-size: 9px; letter-spacing: 1.6px; color: var(--light-text);
  }
  .promo {
    position: absolute; left: 0; right: 0; top: 229px; text-align: center;
    font-size: 13px; color: var(--light-text);
  }
  .promo__highlight { color: var(--accent); }
</style>
</head>
<body>

  <section class="card card--front" aria-label="Business card front">
    <div class="wordmark"><span class="wordmark__square"></span>QUORVANEX</div>
    <div class="tagline">YOUR STRENGTH COMPANION</div>

    <h1 class="holder-name">Lorraine K. Vestal</h1>
    <p class="holder-role">CEO</p>
    <div class="holder-rule"></div>

    <ul class="contact-list">
      <li>
        <svg viewBox="0 0 12 12" aria-hidden="true"><path d="M2.5 1h2l1 2.6-1.3 1A6 6 0 0 0 7.4 7.8l1-1.3L11 7.5v2c0 .8-.7 1.5-1.5 1.4A9 9 0 0 1 1 2.5C1 1.7 1.7 1 2.5 1z"/></svg>
        555.417.3820
      </li>
      <li>
        <svg viewBox="0 0 12 12" aria-hidden="true"><path d="M1 2.5h10v7H1z"/><path d="M1.4 3l4.6 3.6L10.6 3" fill="none" stroke="#ffffff" stroke-width="0.9"/></svg>
        LVestal@Quorvanexco.com
      </li>
      <li>
        <svg viewBox="0 0 12 12" aria-hidden="true"><circle cx="6" cy="6" r="5.2"/></svg>
        www.quorvanexco.com
      </li>
    </ul>

    <address class="postal">
      P.O. Box 47315<br>
      Larkmoor, Vermont 00000
    </address>
  </section>

  <section class="card card--back" aria-label="Business card back">
    <div class="wordmark"><span class="wordmark__square"></span>QUORVANEX</div>
    <div class="tagline">YOUR STRENGTH COMPANION</div>
    <p class="promo"><span class="promo__highlight">Sign up</span> on our website for a coupon code</p>
  </section>

</body>
</html>
```